New, modern business card for growing audiology practice

We need a new business card for our audiology practice. Our logo and website have recently changed (more modern) and we want our business cards to reflect this change.
We conduct hearing tests, perform earwax removals, and fit & dispense hearing aids to our patients. We are a family owned practice in which the owner is the one who works directly with the patient. I have attached logos in various formats to use, as well as two ideas I found on this website; as well as a scanned copy of our current logo. Good luck!

Industry/Entity Type

Business

Contact Information for Business Card

Company name: Tolvera Hearing Center
Provider name: Peter Wolstenby, Au.D. F/NSB
Phone number: (440) 683-5127
Address: 837 W. Lindell Ave. Marrowfield, OH 44391
email: tolverahearing@postvane.com
website: tolverahearing.com

Colors
000000
aaaaaa
dbdbdb
cacaca
9bcb3c
afd23c
cadf82
b1b1b1

Requirements
Must have
• My card must include information in the "details" section. In the attached images, I found a few that I liked and I would like to model after - "brisky bouncin'" and "Sound Method Center".
• Must be horizontal.
• Must include logos provided. I uploaded them in various file formats and various ways.
• Must match logo font, if possible, if not, please get as close as you can.
Nice to have
• I really like the idea of having a color on one side with just the logo and company name and the contact information and provider name on the other side. I also really like the idea of having the main color dominating on the logo/company side with accent of that same color on the contact side of the card.
Should not have
• Must not be vertical.

```html
<!DOCTYPE html>
<html lang="en">
<head>
<meta charset="utf-8">
<title>Tolvera Hearing Center — Business Card</title>
<link rel="stylesheet" href="https://fonts.googleapis.com/css2?family=Lato:wght@400&family=Roboto:wght@400;500&family=Roboto+Condensed:wght@700&display=swap">
<style>
  :root {
    --page: #e9e9e6;
    --card-white: #f4f4f4;
    --brand-green: #6f9e35;
    --ink: #111111;
    --ink-soft: #555555;
    --on-green: #ffffff;
  }
  * { box-sizing: border-box; margin: 0; padding: 0; }
  html, body { width: 1200px; height: 960px; overflow: hidden; }
  body { background: var(--page); position: relative; font-family: "Roboto", Arial, sans-serif; }

  .card { position: absolute; box-shadow: 0 2px 4px rgba(0,0,0,.18); overflow: hidden; }

  /* Contact side */
  .card-front { left: 314px; top: 113px; width: 601px; height: 343px; background: var(--card-white); }
  .card-front .accents { position: absolute; inset: 0; }
  .brand-name {
    position: absolute; right: 34px; top: 33px;
    font-family: "Lato", Arial, sans-serif; font-weight: 400;
    font-size: 17px; letter-spacing: .2px; color: var(--ink);
    display: flex; align-items: center; gap: 8px; white-space: nowrap;
  }
  .brand-dot { width: 12px; height: 12px; border-radius: 50%; background: var(--brand-green); }
  .provider { position: absolute; left: 32px; top: 155px; }
  .provider-name {
    font-family: "Roboto Condensed", Arial, sans-serif; font-weight: 700;
    font-size: 21px; color: var(--brand-green); line-height: 1;
  }
  .provider-title { margin-top: 7px; font-weight: 500; font-size: 14.5px; color: var(--ink); letter-spacing: .3px; }
  .address { position: absolute; left: 32px; top: 211px; font-size: 14px; line-height: 18px; color: var(--ink-soft); font-style: normal; }
  .contacts { position: absolute; left: 32px; top: 257px; list-style: none; font-size: 14px; color: var(--ink-soft); }
  .contacts li { display: flex; align-items: center; height: 19px; }
  .contacts svg { width: 13px; height: 13px; margin-right: 9px; fill: var(--brand-green); flex: none; }

  /* Brand side */
  .card-back { left: 311px; top: 472px; width: 600px; height: 342px; background: var(--brand-green); }
  .back-brand {
    position: absolute; left: 0; right: 0; top: 155px; text-align: center;
    font-family: "Lato", Arial, sans-serif; font-weight: 400;
    font-size: 29px; color: var(--on-green); white-space: nowrap;
  }
  .back-web {
    position: absolute; left: 0; right: 0; top: 287px; text-align: center;
    font-size: 14px; letter-spacing: 3.6px; color: var(--on-green);
  }
</style>
</head>
<body>
  <section class="card card-front" aria-label="Contact side">
    <svg class="accents" width="601" height="343" viewBox="0 0 601 343" aria-hidden="true">
      <path d="M0 0 H131 C70 20 20 70 0 132 Z" fill="var(--brand-green)"/>
      <path d="M601 205 C585 275 540 325 471 343 H601 Z" fill="var(--ink)"/>
    </svg>
    <div class="brand-name"><span class="brand-dot"></span>TOLVERA HEARING CENTER</div>
    <div class="provider">
      <p class="provider-name">PETER WOLSTENBY</p>
      <p class="provider-title">AU.D. F/NSB</p>
    </div>
    <address class="address">837 W. Lindell Ave.<br>Marrowfield, OH 44391</address>
    <ul class="contacts">
      <li><svg viewBox="0 0 24 24"><path d="M6.6 10.8a15 15 0 0 0 6.6 6.6l2.2-2.2c.3-.3.7-.4 1-.2 1.1.4 2.3.6 3.6.6.6 0 1 .4 1 1V20c0 .6-.4 1-1 1A17 17 0 0 1 3 4c0-.6.4-1 1-1h3.5c.6 0 1 .4 1 1 0 1.3.2 2.5.6 3.6.1.3 0 .7-.2 1z"/></svg>(440) 683-5127</li>
      <li><svg viewBox="0 0 24 24"><path d="M2 5h20v2l-10 6L2 7zM2 9l10 6 10-6v10H2z"/></svg>tolverahearing@postvane.com</li>
      <li><svg viewBox="0 0 24 24"><circle cx="12" cy="12" r="10"/><path d="M7 8c2 0 3 1 3 3s2 2 2 4-1 3-2 4M14 4c0 2 1 3 3 3s3 1 4 3" stroke="var(--card-white)" stroke-width="1.6" fill="none"/></svg>tolverahearing.com</li>
    </ul>
  </section>

  <section class="card card-back" aria-label="Brand side">
    <p class="back-brand">TOLVERA HEARING CENTER</p>
    <p class="back-web">www.tolverahearing.com</p>
  </section>
</body>
</html>
```